Music Quizz Application

Hello,

I want a new design for my Blind test (music quizz) application on Korvex. You will find attached the images I want to replace. I need something with the same element (menu / song title) but with a different look!

Same, new icon, you have carte blanche to this one.

I am looking for something fresh…. I'm looking for something with a real artistic choice, contrast, colours, etc.

As a marketing screenshot, I want something classic, you'll find an example attached, feel free to innovate.

To sum-up :

- One new view for my App
- One new icon
- One marketing screenshot

screen resolution :
640×960
icon resolution :
1024x1024

Target Market(s)

15-30 years

Industry/Entity Type

Marketing

```html
<!DOCTYPE html>
<html lang="en">
<head>
<meta charset="utf-8">
<title>Tunequest – Home</title>
<link rel="stylesheet" href="https://fonts.googleapis.com/css2?family=Ubuntu:wght@500;700&family=Arimo:wght@700&display=swap">
<style>
  :root {
    --bar-bg: #000000;
    --bar-text: #d8d8d8;
    --ink: #1a1716;
    --accent: #ff3a0a;
    --menu-top: #403d3b;
    --menu-bottom: #141211;
    --menu-text: #f1efed;
    --divider: #6b6866;
    --divider-shadow: #0c0b0a;
  }
  * { margin: 0; padding: 0; box-sizing: border-box; }
  html, body { width: 800px; height: 1200px; overflow: hidden; background: #000; }
  .screen { position: relative; width: 800px; height: 1200px; overflow: hidden; }

  .backdrop {
    position: absolute; inset: 52px 0 0 0;
    background:
      radial-gradient(ellipse 260px 220px at 40px 300px, #4fd3a6 0%, rgba(79,211,166,0) 100%),
      radial-gradient(ellipse 300px 260px at 720px 180px, #c8401c 0%, rgba(200,64,28,0) 100%),
      radial-gradient(ellipse 340px 260px at 640px 420px, #ffc43a 0%, rgba(255,196,58,0) 100%),
      radial-gradient(ellipse 240px 220px at 80px 100px, #0f1a10 0%, rgba(15,26,16,0) 100%),
      radial-gradient(ellipse 300px 200px at 330px 130px, #2a2414 0%, rgba(42,36,20,0) 100%),
      radial-gradient(ellipse 240px 260px at 30px 900px, #7fe6b4 0%, rgba(127,230,180,0) 100%),
      radial-gradient(ellipse 500px 320px at 400px 1150px, #0a0a0c 0%, rgba(10,10,12,0) 100%),
      radial-gradient(ellipse 260px 240px at 760px 1100px, #7a2a14 0%, rgba(122,42,20,0) 100%),
      radial-gradient(ellipse 420px 380px at 400px 640px, #ffffff 0%, #fff6e6 45%, rgba(255,246,230,0) 100%),
      linear-gradient(180deg, #4a3c20 0%, #e9e2c8 45%, #d9d6c6 70%, #1a1614 100%);
  }

  .status-bar {
    position: absolute; top: 0; left: 0; width: 800px; height: 52px;
    background: var(--bar-bg); color: var(--bar-text);
    font-family: "Arimo", Arial, sans-serif; font-weight: 700; font-size: 29px;
  }
  .status-bar .carrier { position: absolute; left: 10px; top: 11px; display: flex; align-items: flex-end; gap: 10px; }
  .status-bar .signal { display: flex; align-items: flex-end; gap: 3px; padding-bottom: 6px; }
  .status-bar .signal span { width: 4px; height: 3px; background: var(--bar-text); }
  .status-bar .signal span:first-child { height: 12px; width: 6px; }
  .status-bar .network { margin-left: 12px; font-size: 26px; }
  .status-bar .clock { position: absolute; left: 0; width: 800px; top: 11px; text-align: center; font-size: 30px; }
  .status-bar .power { position: absolute; right: 12px; top: 9px; display: flex; align-items: center; gap: 12px; }

  .brand {
    position: absolute; left: 0; width: 800px; top: 318px;
    display: flex; flex-direction: column; align-items: center; gap: 30px;
  }
  .brand-dot { width: 160px; height: 160px; border-radius: 50%; background: var(--accent); }
  .brand-name {
    font-family: "Ubuntu", sans-serif; font-weight: 700;
    font-size: 90px; line-height: 1; color: var(--ink); letter-spacing: -1px;
  }

  .main-menu {
    position: absolute; left: 157px; top: 737px; width: 487px; height: 277px;
    border-radius: 5px; border: 1px solid #2a2826;
    background: linear-gradient(180deg, var(--menu-top) 0%, #262321 45%, var(--menu-bottom) 100%);
    box-shadow: 0 2px 6px rgba(0,0,0,0.45);
    list-style: none;
    font-family: "Ubuntu", sans-serif; font-weight: 500; font-size: 25px; color: var(--menu-text);
  }
  .main-menu .menu-item {
    position: absolute; left: 0; width: 100%; text-align: center; line-height: 30px;
  }
  .main-menu .item-quick { top: 40px; }
  .main-menu .item-blind { top: 128px; }
  .main-menu .item-challenge { top: 213px; }
  .main-menu .divider {
    position: absolute; left: 62px; width: 362px; height: 2px;
    background: var(--divider); border-bottom: 1px solid var(--divider-shadow);
  }
  .main-menu .divider-one { top: 96px; }
  .main-menu .divider-two { top: 181px; }
</style>
</head>
<body>
<div class="screen">
  <div class="backdrop" role="img" aria-label="Blurred colourful bokeh background in green, yellow, orange and dark tones"></div>

  <header class="status-bar">
    <div class="carrier">
      <div class="signal"><span></span><span></span><span></span><span></span><span></span></div>
      <span class="carrier-name">Nova</span>
      <span class="network">3G</span>
    </div>
    <div class="clock">12:14</div>
    <div class="power">
      <span class="battery-level">89 %</span>
      <svg width="46" height="26" viewBox="0 0 46 26" aria-hidden="true">
        <rect x="1.5" y="1.5" width="38" height="23" rx="3" fill="none" stroke="#d8d8d8" stroke-width="3"/>
        <rect x="40" y="8" width="4" height="10" fill="#d8d8d8"/>
        <rect x="5" y="5" width="31" height="16" fill="#d8d8d8"/>
        <path d="M23 5 L15 14 L21 14 L18 21 L27 11 L21 11 Z" fill="#000"/>
      </svg>
    </div>
  </header>

  <div class="brand">
    <div class="brand-dot"></div>
    <div class="brand-name">Tunequest</div>
  </div>

  <ul class="main-menu">
    <li class="menu-item item-quick">Quick Game</li>
    <li class="divider divider-one" role="separator"></li>
    <li class="menu-item item-blind">Blind Test</li>
    <li class="divider divider-two" role="separator"></li>
    <li class="menu-item item-challenge">Challenge</li>
  </ul>
</div>
</body>
</html>
```